Harrow Tavern & Grille Menu Makeover

I am looking for a professional look to update our current menu. We are an independently owned sports bar and grill. Up to this point, I have done all of my own graphic designing. I am looking for something classy/family oriented. We are a very family friendly sports bar that offers a wide variety of menu options. Our website is www.harrowtavernco.example. This may help you get more of a feel for what type of place we are and what we offer. Our menu is listed on the website. My current menu is 8.5x14 inserts that feature a cover page, 4 inside pages and a back page. I would like something a little more condensed than this. Possibly a large tri-fold menu? I am open to all new ideas. I do have some pictures on my menu now, and would like to continue using a few pictures to feature some of my items. I would like something that is in a format that gives me the option to change items and prices on my own in the future. I would also like it to feature, or inform my patrons about our technology that we offer. We offer online ordering and we are a "verified venue" with Brewvoke.( a social site for craft beer lovers).

Industry/Entity Type

Sports Bar

Requirements
Nice to have
• Nice to have some pictures, but does not have to. We do feature 9 different beers on tap. A lot of them are local craft beers from the state of Kansas. Not sure if that is something we can feature, but it is a nice talking point. All of our tables and bar are hand built. With a rich mahogany finish on all of our woodwork, some type of "woodgrain" look into the menu would be nice.

```html
<!DOCTYPE html>
<html lang="en">
<head>
<meta charset="utf-8">
<title>Harrow Tavern &amp; Grille – Entrees &amp; Salads</title>
<link href="https://fonts.googleapis.com/css2?family=Alfa+Slab+One&family=Oswald:wght@400;600&display=swap" rel="stylesheet">
<style>
:root{
  --edge:#2a170d;
  --parchment:#ead8b0;
  --parchment-deep:#c8a46d;
  --heading:#7b2616;
  --ink:#3a2213;
  --ink-soft:#5a3b22;
  --footer-ink:#e6d3ad;
  --photo-a:#7a4a26;
  --photo-b:#3d5a22;
}
*{margin:0;padding:0;box-sizing:border-box}
html,body{width:851px;height:1200px;overflow:hidden;background:var(--edge)}
.menu{position:relative;width:851px;height:1200px;background:var(--edge)}
.parchment{position:absolute;left:14px;top:8px;width:823px;height:1150px;
  background:radial-gradient(ellipse at 50% 45%,var(--parchment) 55%,var(--parchment-deep) 100%);
  border-radius:6px 14px 8px 12px}
.section-title{position:absolute;left:40px;font-family:"Alfa Slab One",serif;font-size:36px;color:var(--heading);letter-spacing:1px}
.column{position:absolute;width:252px;font-family:"Oswald",sans-serif;color:var(--ink)}
.item{margin-bottom:9px}
.item h3{font-size:9px;font-weight:600;letter-spacing:.3px;text-transform:uppercase;line-height:11px}
.item p{font-size:5.6px;line-height:7px;color:var(--ink-soft);text-transform:uppercase}
.photo{position:absolute;border-radius:50%;border:3px solid var(--ink)}
.photo-entree{left:592px;top:70px;width:92px;height:92px;background:radial-gradient(circle at 45% 45%,#b07a45,var(--photo-a) 60%,#2e1a0e)}
.photo-salad{left:594px;top:460px;width:92px;height:92px;background:radial-gradient(circle at 45% 45%,#9b3a2a,var(--photo-b) 55%,#24301a)}
.note{position:absolute;left:180px;top:366px;width:400px;text-align:center;font-family:"Oswald",sans-serif;font-size:5.6px;line-height:7px;color:var(--ink-soft);text-transform:uppercase}
.divider{position:absolute;left:260px;top:390px}
.social{position:absolute;top:722px;left:180px;width:420px;display:flex;justify-content:space-between;font-family:"Oswald",sans-serif;font-size:7px;font-weight:600;color:var(--ink);text-transform:uppercase}
.social span{display:flex;align-items:center;gap:4px}
.social i{display:inline-block;width:8px;height:8px;border-radius:50%;background:var(--ink)}
.footnote{position:absolute;left:0;top:1172px;width:851px;text-align:center;font-family:"Oswald",sans-serif;font-size:6px;letter-spacing:.3px;color:var(--footer-ink);text-transform:uppercase}
</style>
</head>
<body>
<main class="menu">
  <div class="parchment"></div>

  <h1 class="section-title" style="top:40px">ENTREES</h1>

  <section class="column" style="left:40px;top:92px">
    <div class="item"><h3>Chicken Strip Basket</h3><p>Hand breaded chicken strips served with fries and your choice of dipping sauce. Small 7.99 / Large 9.99</p></div>
    <div class="item"><h3>Smothered Chicken Breast Fillet</h3><p>Grilled chicken breast topped with sauteed onions, mushrooms and melted swiss cheese, served with two sides. 10.99</p></div>
    <div class="item"><h3>Blackened Tilapia</h3><p>Two tilapia fillets seasoned with cajun spices, seared and served with rice and a side. 11.49</p></div>
    <div class="item"><h3>Beer Fried Catfish</h3><p>Catfish fillets dipped in craft beer batter, fried golden, served with slaw and fries. 11.99</p></div>
    <div class="item"><h3>Pepper Jack Burger Steak</h3><p>Seasoned ground beef patty topped with pepper jack cheese and grilled jalapenos, with two sides. 10.49</p></div>
    <div class="item"><h3>St. Louis Ribs</h3><p>Slow smoked pork ribs brushed with house barbecue sauce. Half rack 13.99 / Full rack 19.99</p></div>
    <div class="item"><h3>Pork Stuffed Baked Potato</h3><p>A giant baked potato loaded with pulled pork, cheddar, bacon, sour cream and green onions, served with a side salad. 9.99</p></div>
  </section>

  <section class="column" style="left:318px;top:66px">
    <div class="item"><h3>Harrow Loaded Chicken</h3><p>Grilled chicken breast topped with bacon, barbecue sauce, cheddar and jack cheese with two sides. 11.49</p></div>
    <div class="item"><h3>Chicken Fried Chicken Dinner</h3><p>Crispy breaded chicken breast smothered in country gravy, served with mashed potatoes and a vegetable. 10.99</p></div>
    <div class="item"><h3>Fried Shrimp</h3><p>Golden fried shrimp served with fries, slaw and cocktail sauce. Small 9.49 / Large 12.99</p></div>
    <div class="item"><h3>Country Fried Steak</h3><p>Tenderized steak hand breaded and topped with country gravy, served with two sides. 10.99</p></div>
    <div class="item"><h3>Black N' Blue Sirloin</h3><p>Eight ounce sirloin blackened and topped with blue cheese crumbles, with two sides. 15.99</p></div>
    <div class="item"><h3>Iron Griddle Steak</h3><p>Hand cut steak seared on the iron griddle with onions and peppers. 14.49</p></div>
    <div class="item"><h3>Flat Iron Steak</h3><p>Tender flat iron steak grilled to order, served with garlic butter and two sides. 16.99</p></div>
  </section>

  <div class="photo photo-entree" role="img" aria-label="Round photo of a featured grilled entree plate"></div>

  <p class="note">Consuming raw or undercooked meats, poultry, seafood, shellfish or eggs may increase your risk of foodborne illness.</p>
  <svg class="divider" width="330" height="12" viewBox="0 0 330 12" aria-hidden="true">
    <line x1="0" y1="6" x2="140" y2="6" stroke="#3a2213" stroke-width="1"/>
    <circle cx="165" cy="6" r="3" fill="#3a2213"/>
    <line x1="190" y1="6" x2="330" y2="6" stroke="#3a2213" stroke-width="1"/>
  </svg>

  <h1 class="section-title" style="top:412px">SALADS</h1>

  <section class="column" style="left:40px;top:462px">
    <div class="item"><h3>Chicken Tender Garden Salad</h3><p>A bed of crisp greens topped with breaded chicken tenders, tomatoes, cucumbers, egg and cheddar cheese with your choice of dressing. Small 7.49 / Large 9.49</p></div>
    <div class="item"><h3>Nacho Crunch Salad</h3><p>Seasoned ground beef over lettuce with tomatoes, onions, cheddar and crushed nacho chips, served with salsa and sour cream. Small 7.49 / Large 9.49</p></div>
    <div class="item"><h3>Cobb Salad</h3><p>Mixed greens with grilled chicken, bacon, egg, avocado, tomato and blue cheese crumbles. Small 7.99 / Large 9.99</p></div>
    <div class="item"><h3>Summer Berry Salad</h3><p>Spring mix with strawberries, blueberries, candied pecans and feta cheese, served with raspberry vinaigrette. Add grilled chicken for 2.00. Small 7.49 / Large 9.49</p></div>
  </section>

  <section class="column" style="left:318px;top:462px">
    <div class="item"><h3>House Caesar Salad</h3><p>Crisp romaine tossed with caesar dressing, shaved parmesan and croutons. Add grilled or crispy chicken for 2.00. Small 6.49 / Large 8.49</p></div>
    <div class="item"><h3>Nacho Crunch Salad</h3><p>Crunchy nacho chips over iceberg lettuce topped with taco meat, tomatoes, onions, jalapenos and cheddar with salsa ranch. Small 7.49 / Large 9.49</p></div>
    <div class="item"><h3>Chef Salad</h3><p>Fresh greens with ham, turkey, bacon, egg, tomatoes, cucumbers and shredded cheese with your choice of dressing. Small 7.99 / Large 9.99</p></div>
    <div class="item"><h3>Summer Berry Salad</h3><p>Fresh spinach with berries, mandarin oranges, almonds and goat cheese, tossed in poppyseed dressing. Small 7.49 / Large 9.49</p></div>
  </section>

  <div class="photo photo-salad" role="img" aria-label="Round photo of a fresh garden salad"></div>

  <div class="social">
    <span><i></i>harrowtaverngrille</span>
    <span><i></i>www.harrowtavernco.example</span>
    <span><i></i>Brewvoke</span>
  </div>

  <p class="footnote">When splitting a large topping, you will be charged the price of a small topping if a small portion is ordered.</p>
</main>
</body>
</html>
```